Need Web Design for Business Process Outsourcing Company (Quorvane)

Quorvane is a business process outsourcing company. Need a simple site similar to http://www.tallowbrinkhire.com/ but with a more professional and credible look. New to the process; not sure where to start and comparing my options. Please let me know what my options are if I choose to go with you. Logo is attached for your reference. Please use same colorway

Reason: I want the final product to be coded. Please confirm you will be able to code final design.

Industry/Entity Type

Business

Coding

Coded - Design and coding required

```html
<!DOCTYPE html>
<html lang="en">
<head>
<meta charset="utf-8">
<title>Quorvane Services</title>
<link href="https://fonts.googleapis.com/css2?family=Open+Sans:wght@400;600;700;800&display=swap" rel="stylesheet">
<style>
:root{
  --blue:#1b8fd8;
  --blue-dark:#1272b3;
  --navy:#14304f;
  --navy-deep:#0c1f36;
  --ink:#2c3440;
  --text:#7a808a;
  --grey-band:#eceef1;
  --line:#dfe3e8;
  --white:#ffffff;
}
*{box-sizing:border-box;margin:0;padding:0}
html,body{width:1200px;height:2416px;overflow:hidden}
body{font-family:"Open Sans",Arial,sans-serif;color:var(--text);background:var(--white);position:relative;font-size:14px;line-height:1.6}
a{color:inherit;text-decoration:none}

/* Header + hero */
.hero{position:absolute;left:0;top:0;width:1200px;height:540px;overflow:hidden}
.hero-photo{position:absolute;inset:0;background:linear-gradient(160deg,#5d7ea3 0%,#2b4d75 35%,#13304f 70%,#0b1d33 100%)}
.hero-cut{position:absolute;left:0;bottom:0;width:1200px;height:120px}
.brand{position:absolute;left:40px;top:24px;display:flex;align-items:center;gap:12px}
.brand-mark{width:34px;height:34px;background:var(--blue)}
.brand-name{font-size:32px;font-weight:700;color:var(--white);letter-spacing:.5px}
.topbar{position:absolute;right:60px;top:16px;display:flex;gap:28px;font-size:14px;color:var(--white)}
.topbar span{display:flex;align-items:center;gap:8px}
.topbar svg{width:16px;height:16px}
.nav{position:absolute;right:60px;top:52px;display:flex;gap:4px;font-size:14px;color:var(--white);font-weight:600}
.nav a{padding:10px 14px}
.nav a.active{background:var(--blue)}
.nav svg{width:16px;height:16px;margin:12px 0 0 10px}
.hero-title{position:absolute;top:150px;width:100%;text-align:center;color:var(--white);font-size:62px;font-weight:700;letter-spacing:.5px}
.hero-sub{position:absolute;top:232px;width:100%;text-align:center;color:var(--white);font-size:30px;font-weight:600}
.btn-quote{position:absolute;top:322px;left:508px;width:184px;height:40px;background:var(--blue);color:var(--white);font-size:13px;font-weight:700;letter-spacing:.5px;display:flex;align-items:center;justify-content:center}
.hero-dots{position:absolute;top:474px;left:0;width:100%;display:flex;justify-content:center;gap:8px}
.hero-dots i{width:10px;height:10px;border-radius:50%;border:1px solid var(--white)}
.hero-dots i.on{background:var(--white)}
.live-chat{position:absolute;right:0;top:270px;width:32px;height:120px;background:var(--navy-deep);color:var(--white);font-size:12px;font-weight:700;writing-mode:vertical-rl;display:flex;align-items:center;justify-content:center;letter-spacing:2px}

/* Section headings */
.section-title{text-align:center;font-size:24px;font-weight:700;color:var(--ink);letter-spacing:.5px}
.section-title::after{content:"";display:block;width:50px;height:3px;background:var(--blue);margin:10px auto 0}

/* Welcome */
.welcome{position:absolute;top:612px;left:0;width:1200px;height:360px}
.welcome-body{display:flex;justify-content:space-between;padding:0 100px;margin-top:34px}
.welcome-text{width:540px}
.welcome-lead{color:var(--blue);font-size:17px;font-weight:600;line-height:1.45;margin-bottom:14px}
.welcome-text p{font-size:13px;margin-bottom:10px}
.btn-outline{display:inline-block;border:1px solid var(--blue);color:var(--blue);font-size:12px;font-weight:700;padding:7px 18px;margin-top:6px}
.video{position:relative;width:340px;height:268px;background:linear-gradient(135deg,#3d6b99 0%,#1d3e66 50%,#0f243f 100%)}
.video .play{position:absolute;left:140px;top:104px;width:60px;height:60px}

/* Services */
.services{position:absolute;top:1000px;left:0;width:1200px;height:390px;background:var(--grey-band);padding-top:44px}
.service-grid{display:flex;justify-content:space-between;padding:0 110px;margin-top:40px}
.service{width:210px;text-align:center}
.service-icon{width:88px;height:88px;margin:0 auto 16px;border-radius:50%;background:var(--blue);display:flex;align-items:center;justify-content:center}
.service-icon svg{width:44px;height:44px}
.service h3{color:var(--ink);font-size:18px;font-weight:700;margin-bottom:6px}
.service p{font-size:12px;line-height:1.55;margin-bottom:10px}
.read-more{color:var(--blue);font-size:12px;font-weight:700}

/* Why + news */
.split{position:absolute;top:1430px;left:0;width:1200px;height:440px;display:flex;justify-content:space-between;padding:0 100px}
.col-title{font-size:24px;font-weight:700;color:var(--ink)}
.col-title::after{content:"";display:block;width:50px;height:3px;background:var(--blue);margin-top:8px}
.why{width:470px}
.why .intro{font-size:13px;margin:16px 0 12px}
.why ul{list-style:none}
.why li{display:flex;gap:12px;align-items:flex-start;font-size:13px;padding:8px 0;border-bottom:1px solid var(--line)}
.why li svg{flex:none;width:18px;height:18px;margin-top:2px}
.news{width:500px}
.news-item{display:flex;gap:18px;margin-top:22px;padding-bottom:18px;border-bottom:1px solid var(--line)}
.news-thumb{flex:none;width:170px;height:110px}
.news-thumb.one{background:linear-gradient(135deg,#b8c7d6,#5a7896)}
.news-thumb.two{background:linear-gradient(135deg,#3e6c9f,#142e52)}
.news-item h4{color:var(--blue);font-size:13px;font-weight:700;line-height:1.4}
.news-meta{font-size:11px;color:#9aa0a8;margin:6px 0;display:flex;gap:14px}
.news-item p{font-size:12px;line-height:1.5}
.split .btn-outline{margin-top:14px}

/* Testimonial */
.testimonial{position:absolute;top:1880px;left:0;width:1200px;height:230px}
.testimonial svg.band{position:absolute;inset:0;width:1200px;height:230px}
.quote{position:absolute;left:150px;top:70px;display:flex;gap:36px;align-items:center;color:var(--white);width:900px}
.quote-photo{flex:none;width:110px;height:110px;border-radius:50%;background:linear-gradient(135deg,#a9b9c9,#3c5876);border:4px solid var(--white)}
.quote p{font-size:14px;font-style:normal;line-height:1.6}
.quote strong{display:block;margin-top:10px;font-size:13px;letter-spacing:1px}
.quote-dots{position:absolute;top:2136px;left:0;width:1200px;display:flex;justify-content:center;gap:8px}
.quote-dots i{width:10px;height:10px;border-radius:50%;border:1px solid var(--blue)}
.quote-dots i.on{background:var(--blue)}

/* Footer */
.footer{position:absolute;top:2176px;left:0;width:1200px;height:184px;display:flex;justify-content:space-between;padding:0 100px}
.footer-brand{width:330px}
.footer-brand .brand-name{color:var(--blue);font-size:36px}
.footer-brand .line{display:flex;align-items:center;gap:12px}
.footer-brand p{font-size:12px;margin-top:14px;line-height:1.6}
.footer h5{color:var(--ink);font-size:15px;font-weight:700;letter-spacing:.5px;margin-bottom:14px}
.contact{width:250px}
.contact div{display:flex;gap:10px;align-items:flex-start;font-size:12px;margin-bottom:10px}
.contact svg{flex:none;width:14px;height:14px;margin-top:2px}
.locations{width:300px}
.map{width:300px;height:130px;background:linear-gradient(180deg,#dfe5ec,#c7d2dd)}
.bottom-bar{position:absolute;top:2360px;left:0;width:1200px;height:56px;background:#f3f4f6;display:flex;align-items:center;justify-content:space-between;padding:0 100px;font-size:12px;border-top:1px solid var(--line)}
.socials{display:flex;gap:10px}
.socials i{width:28px;height:28px;border-radius:50%;border:1px solid #aab1ba}
</style>
</head>
<body>

<header class="hero">
  <div class="hero-photo" role="img" aria-label="Photograph looking up at glass office towers in blue tones"></div>
  <svg class="hero-cut" viewBox="0 0 1200 120" preserveAspectRatio="none">
    <polygon points="0,70 1200,0 1200,120 0,120" fill="#ffffff"/>
    <polygon points="0,70 420,45 0,92" fill="#1b8fd8"/>
  </svg>

  <a class="brand" href="#"><span class="brand-mark"></span><span class="brand-name">Quorvane</span></a>

  <div class="topbar">
    <span><svg viewBox="0 0 16 16"><path d="M3 1h3l1.5 4-2 1.2a9 9 0 0 0 4.3 4.3L11 8.5l4 1.5v3a2 2 0 0 1-2 2A12 12 0 0 1 1 3a2 2 0 0 1 2-2z" fill="#fff"/></svg>800 555 0142</span>
    <span><svg viewBox="0 0 16 16"><rect x="1" y="3" width="14" height="10" fill="none" stroke="#fff" stroke-width="1.5"/><path d="M1 3l7 6 7-6" fill="none" stroke="#fff" stroke-width="1.5"/></svg>info@quorvane.com</span>
  </div>

  <nav class="nav">
    <a class="active" href="#">Home</a>
    <a href="#">About us</a>
    <a href="#">Services</a>
    <a href="#">Insights</a>
    <a href="#">Blog</a>
    <a href="#">Career</a>
    <a href="#">Contact Us</a>
    <svg viewBox="0 0 16 16"><circle cx="6.5" cy="6.5" r="5" fill="none" stroke="#fff" stroke-width="2"/><path d="M10 10l5 5" stroke="#fff" stroke-width="2"/></svg>
  </nav>

  <h1 class="hero-title">Quorvane Services</h1>
  <p class="hero-sub">We are a BPO business process outsourcing company</p>
  <a class="btn-quote" href="#">GET A FREE QUOTE</a>
  <div class="hero-dots"><i class="on"></i><i></i><i></i></div>
  <div class="live-chat">LIVE CHAT</div>
</header>

<section class="welcome">
  <h2 class="section-title">WELCOME TO QUORVANE</h2>
  <div class="welcome-body">
    <div class="welcome-text">
      <p class="welcome-lead">We simplify complex back-office work so growing teams can focus on what matters most</p>
      <p>We take care of the everyday processes that slow your business down, from data handling and billing to customer care and payroll support.</p>
      <p>Our trained teams work as an extension of yours, following your standards, your tools and your timelines while keeping costs predictable and quality high.</p>
      <p>Every engagement starts with a clear review of your workflows so we can recommend the right mix of people, process and technology for you.</p>
      <a class="btn-outline" href="#">READ MORE &gt;&gt;</a>
    </div>
    <div class="video" role="img" aria-label="Video still of a businessman touching a digital network interface">
      <svg class="play" viewBox="0 0 60 60"><circle cx="30" cy="30" r="28" fill="rgba(0,0,0,.55)" stroke="#fff" stroke-width="2"/><polygon points="24,18 44,30 24,42" fill="#fff"/></svg>
    </div>
  </div>
</section>

<section class="services">
  <h2 class="section-title">QUORVANE SERVICES</h2>
  <div class="service-grid">
    <div class="service">
      <div class="service-icon"><svg viewBox="0 0 44 44"><rect x="5" y="8" width="34" height="22" rx="2" fill="none" stroke="#fff" stroke-width="3"/><path d="M16 38h12M22 30v8" stroke="#fff" stroke-width="3"/></svg></div>
      <h3>IT Solutions</h3>
      <p>Managed infrastructure, helpdesk and application support delivered by certified engineers around the clock.</p>
      <a class="read-more" href="#">READ MORE &gt;&gt;</a>
    </div>
    <div class="service">
      <div class="service-icon"><svg viewBox="0 0 44 44"><path d="M9 24v-4a13 13 0 0 1 26 0v4" fill="none" stroke="#fff" stroke-width="3"/><rect x="6" y="22" width="7" height="11" rx="2" fill="#fff"/><rect x="31" y="22" width="7" height="11" rx="2" fill="#fff"/><path d="M34 33c0 4-4 6-10 6" fill="none" stroke="#fff" stroke-width="2.5"/></svg></div>
      <h3>Customer Support</h3>
      <p>Friendly multilingual agents handling calls, chat and email with clear service levels.</p>
      <a class="read-more" href="#">READ MORE &gt;&gt;</a>
    </div>
    <div class="service">
      <div class="service-icon"><svg viewBox="0 0 44 44"><rect x="7" y="24" width="7" height="13" fill="#fff"/><rect x="18" y="16" width="7" height="21" fill="#fff"/><rect x="29" y="8" width="7" height="29" fill="#fff"/></svg></div>
      <h3>Marketing</h3>
      <p>Lead generation, campaign support and market research that keeps your pipeline full.</p>
      <a class="read-more" href="#">READ MORE &gt;&gt;</a>
    </div>
    <div class="service">
      <div class="service-icon"><svg viewBox="0 0 44 44"><circle cx="15" cy="15" r="5" fill="#fff"/><circle cx="29" cy="15" r="5" fill="#fff"/><path d="M5 34a10 10 0 0 1 20 0zM19 34a10 10 0 0 1 20 0z" fill="#fff"/></svg></div>
      <h3>Human Resources</h3>
      <p>Recruitment, onboarding and payroll administration handled with care and full compliance.</p>
      <a class="read-more" href="#">READ MORE &gt;&gt;</a>
    </div>
  </div>
</section>

<section class="split">
  <div class="why">
    <h2 class="col-title">WHY CHOOSE US</h2>
    <p class="intro">We combine experienced people, proven methods and secure systems to deliver outsourcing you can rely on.</p>
    <ul>
      <li><svg viewBox="0 0 18 18"><circle cx="9" cy="9" r="8" fill="none" stroke="#1b8fd8" stroke-width="1.5"/><path d="M5 9l3 3 5-6" fill="none" stroke="#1b8fd8" stroke-width="1.8"/></svg>Dedicated account managers who know your business inside out</li>
      <li><svg viewBox="0 0 18 18"><circle cx="9" cy="9" r="8" fill="none" stroke="#1b8fd8" stroke-width="1.5"/><path d="M5 9l3 3 5-6" fill="none" stroke="#1b8fd8" stroke-width="1.8"/></svg>Flexible teams that scale up or down as your needs change</li>
      <li><svg viewBox="0 0 18 18"><circle cx="9" cy="9" r="8" fill="none" stroke="#1b8fd8" stroke-width="1.5"/><path d="M5 9l3 3 5-6" fill="none" stroke="#1b8fd8" stroke-width="1.8"/></svg>Secure facilities and strict data protection on every project</li>
      <li><svg viewBox="0 0 18 18"><circle cx="9" cy="9" r="8" fill="none" stroke="#1b8fd8" stroke-width="1.5"/><path d="M5 9l3 3 5-6" fill="none" stroke="#1b8fd8" stroke-width="1.8"/></svg>Transparent reporting with clear metrics every single week</li>
      <li><svg viewBox="0 0 18 18"><circle cx="9" cy="9" r="8" fill="none" stroke="#1b8fd8" stroke-width="1.5"/><path d="M5 9l3 3 5-6" fill="none" stroke="#1b8fd8" stroke-width="1.8"/></svg>Round-the-clock coverage across multiple time zones</li>
      <li><svg viewBox="0 0 18 18"><circle cx="9" cy="9" r="8" fill="none" stroke="#1b8fd8" stroke-width="1.5"/><path d="M5 9l3 3 5-6" fill="none" stroke="#1b8fd8" stroke-width="1.8"/></svg>Competitive pricing with no hidden fees or surprises</li>
    </ul>
    <a class="btn-outline" href="#">READ MORE &gt;&gt;</a>
  </div>
  <div class="news">
    <h2 class="col-title">LATEST NEWS</h2>
    <article class="news-item">
      <div class="news-thumb one" role="img" aria-label="Photo of a business team meeting around a table"></div>
      <div>
        <h4>HOW OUTSOURCING HELPS SMALL TEAMS GROW FASTER WITHOUT ADDING OVERHEAD</h4>
        <div class="news-meta"><span>12.03.2015</span><span>by Admin</span><span>4 Comments</span></div>
        <p>A closer look at how shared services free up time and budget for the work that drives growth.</p>
      </div>
    </article>
    <article class="news-item">
      <div class="news-thumb two" role="img" aria-label="Photo of hands on a laptop with data overlays"></div>
      <div>
        <h4>FIVE QUESTIONS TO ASK BEFORE CHOOSING A BUSINESS PROCESS PARTNER</h4>
        <div class="news-meta"><span>08.03.2015</span><span>by Admin</span><span>3 Comments</span></div>
        <p>Picking the right partner starts with clear goals, honest pricing and a team that understands your sector.</p>
      </div>
    </article>
    <a class="btn-outline" href="#">VIEW MORE &gt;&gt;</a>
  </div>
</section>

<section class="testimonial">
  <svg class="band" viewBox="0 0 1200 230" preserveAspectRatio="none">
    <polygon points="0,40 1200,0 1200,230 0,230" fill="#1b8fd8"/>
    <polygon points="0,40 1200,0 1200,14 0,54" fill="#1272b3"/>
  </svg>
  <div class="quote">
    <div class="quote-photo" role="img" aria-label="Portrait photo of the client giving the testimonial"></div>
    <p>Working with the team has been a turning point for us. Our back-office tasks run smoothly, response times have improved and we finally have the time to focus on our customers and new growth.<strong>MARA ELLISON</strong></p>
  </div>
</section>
<div class="quote-dots"><i class="on"></i><i></i></div>

<footer class="footer">
  <div class="footer-brand">
    <div class="line"><span class="brand-mark"></span><span class="brand-name">Quorvane</span></div>
    <p>We help businesses of every size streamline operations through reliable, affordable and secure outsourcing services.</p>
  </div>
  <div class="contact">
    <h5>CONTACT US</h5>
    <div><svg viewBox="0 0 14 14"><path d="M7 1a4.5 4.5 0 0 1 4.5 4.5C11.5 9 7 13 7 13S2.5 9 2.5 5.5A4.5 4.5 0 0 1 7 1z" fill="#1b8fd8"/><circle cx="7" cy="5.5" r="1.6" fill="#fff"/></svg>24 Harbour Point, Riverton, 4021</div>
    <div><svg viewBox="0 0 16 16"><path d="M3 1h3l1.5 4-2 1.2a9 9 0 0 0 4.3 4.3L11 8.5l4 1.5v3a2 2 0 0 1-2 2A12 12 0 0 1 1 3a2 2 0 0 1 2-2z" fill="#1b8fd8"/></svg>800 555 0142</div>
    <div><svg viewBox="0 0 16 16"><rect x="1" y="3" width="14" height="10" fill="none" stroke="#1b8fd8" stroke-width="1.6"/><path d="M1 3l7 6 7-6" fill="none" stroke="#1b8fd8" stroke-width="1.6"/></svg>info@quorvane.com</div>
  </div>
  <div class="locations">
    <h5>LOCATIONS</h5>
    <div class="map" role="img" aria-label="World map marking office locations"></div>
  </div>
</footer>

<div class="bottom-bar">
  <span>Copyright © 2015, Quorvane Services. All rights reserved.</span>
  <div class="socials"><i></i><i></i><i></i><i></i></div>
</div>

</body>
</html>
```